high end kitchens , needing new logo and business card design .

im looking a very simple looking design but classy that will stand out , i would like the design to be in the colours black , silver , gold and grey , although all colours dont need to be used in design , back of card to have name on it derek fawcett , address and phone number and website address , maybe fb logo . adrress is 42 mill row , glenharrow , bt19 4qa , 07912488265 , front of the card im open to design , back of card very simple i will want it matt black with silver writing , writing doesnt need to be that big

Target Market(s)

people with kitchen projects .

Industry/Entity Type

Interior Design

Contact Information for Business Card

front of business card th on it with maybe tallow hearths under it wrote smaller , maybe the card to be mate black with the writing in a gloss black or silver

Logo Text

th . tallow hearths

Font styles to use
Sans Serif
Script

Colors
1b1b1b
919191
f6f6f6
848484
ffc214
ec1f27

Requirements
Must have
• clean and simple , not too fussy ,
Nice to have
• n/a
Should not have
• n/a

```html
<!DOCTYPE html>
<html lang="en">
<head>
<meta charset="utf-8">
<title>Tallow Hearths – Business Card</title>
<link href="https://fonts.googleapis.com/css2?family=Jost:wght@400&display=swap" rel="stylesheet">
<style>
  :root {
    --backdrop: #8a8a8a;
    --card-black: #1b1b1b;
    --card-edge: #232323;
    --wordmark: #0b0b0b;
    --silver: #bdbdbd;
    --silver-dim: #919191;
  }
  * { margin: 0; padding: 0; box-sizing: border-box; }
  html, body { width: 1200px; height: 900px; overflow: hidden; }
  body {
    background: var(--backdrop);
    font-family: "Jost", sans-serif;
    display: flex;
    flex-direction: column;
    align-items: center;
    justify-content: center;
    gap: 40px;
  }
  .card {
    position: relative;
    width: 660px;
    height: 400px;
    background: radial-gradient(ellipse at 55% 35%, #2a2a2a 0%, var(--card-black) 70%);
    border: 1px solid var(--card-edge);
    overflow: hidden;
  }
  .wordmark {
    color: var(--wordmark);
    font-weight: 400;
    text-transform: uppercase;
    letter-spacing: 0.02em;
    white-space: nowrap;
  }
  .card-front .wordmark {
    position: absolute;
    left: 50%;
    top: 50%;
    transform: translate(-50%, -50%);
    font-size: 44px;
  }
  .card-back .wordmark {
    position: absolute;
    left: 28px;
    top: 18px;
    font-size: 42px;
  }
  .holder-name {
    position: absolute;
    left: 70px;
    top: 190px;
    color: var(--silver);
    font-size: 17px;
    letter-spacing: 0.3em;
    text-transform: uppercase;
    white-space: nowrap;
  }
  .contact-list {
    position: absolute;
    left: 58px;
    top: 240px;
    list-style: none;
    color: var(--silver);
    font-size: 17px;
    line-height: 1.55;
    letter-spacing: 0.04em;
    white-space: nowrap;
  }
  .contact-list .label { display: inline-block; width: 30px; }
  .address {
    position: absolute;
    left: 440px;
    top: 290px;
    color: var(--silver-dim);
    font-size: 17px;
    line-height: 1.5;
    letter-spacing: 0.05em;
    font-style: normal;
    white-space: nowrap;
  }
</style>
</head>
<body>
  <section class="card card-front" aria-label="Card front">
    <span class="wordmark">tallow hearths</span>
  </section>

  <section class="card card-back" aria-label="Card back">
    <span class="wordmark">tallow hearths</span>
    <p class="holder-name">derek fawcett</p>
    <ul class="contact-list">
      <li><span class="label">P:</span>07912488265</li>
      <li><span class="label">E:</span>info@tallowhearths.com</li>
      <li><span class="label">W:</span>www.tallowhearths.com</li>
    </ul>
    <address class="address">
      42 mill row ,<br>
      glenharrow ,<br>
      bt19 4qa
    </address>
  </section>
</body>
</html>
```